Business card for denture clinic Veltrimora

We need a new business card with our new logo. We are a denture clinic in New Zealand with our target market being 45+ years old. We would need a space on the back to write our patients next appointment on. We would space for only one appointment rather than a list. We will attach a photo showing an example of this. But of course, we would like to see your twist on this. We want it to be bold and easy to read and a good mixture of professional but modern. We have attached our logo to be used on the card.

Target Market(s)

People aged 45+ needing dentures

Industry/Entity Type

Dental

Contact Information for Business Card

We want our logo on the front and the space to write an appointment on the back. I've attached an example our our old business card showing this. We need to have the technicians details on the front.

Font styles to use
Sans Serif

Colors
0255a3
919191
fbfbfb

Requirements
Must have
• The following details:
• Liam Dorsett BDT, PGDipCDentTech Calverin
• Dental Prosthetist
• Phone numbers: 0800 47 3125
• 09 572 1394
• Email: liam@veltrimora.co.nz
• www.veltrimora.co.nz
• Address: 14 Marlow Crest Road
• Halbrook West
• Auckland 0793
Nice to have
• We would like our business cards to have more than just two colours as we want them to be more vibrant. We have uploaded an example of a business card we liked that showed this.

```html
<!DOCTYPE html>
<html lang="en">
<head>
<meta charset="UTF-8">
<title>Veltrimora – Business Card</title>
<link href="https://fonts.googleapis.com/css2?family=Exo+2:wght@400;500;600;700&display=swap" rel="stylesheet">
<style>
  :root {
    --brand-blue: #0255a3;
    --mid-blue: #1f78c8;
    --text-grey: #6e6e6e;
    --rule-grey: #919191;
    --card-white: #fbfbfb;
    --backdrop: #ececec;
  }
  * { margin: 0; padding: 0; box-sizing: border-box; }
  html, body {
    width: 1200px;
    height: 900px;
    overflow: hidden;
    background: var(--backdrop);
    font-family: "Exo 2", Arial, sans-serif;
  }
  .canvas {
    position: relative;
    width: 1200px;
    height: 900px;
  }
  .card {
    position: absolute;
    top: 300px;
    width: 520px;
    height: 300px;
    background: var(--card-white);
    box-shadow: 0 2px 6px rgba(0,0,0,0.12);
  }
  .card--front { left: 50px; }
  .card--back { left: 630px; }

  /* Front */
  .holder {
    position: absolute;
    top: 30px;
    left: 34px;
  }
  .holder__name {
    color: var(--brand-blue);
    font-weight: 700;
    font-size: 24px;
    letter-spacing: 0.5px;
    text-transform: uppercase;
  }
  .holder__post {
    font-size: 12px;
    font-weight: 600;
    margin-left: 3px;
  }
  .holder__quals {
    color: var(--mid-blue);
    font-size: 13px;
    font-weight: 500;
    margin-top: 1px;
  }
  .holder__role {
    color: var(--text-grey);
    font-size: 14px;
    font-weight: 700;
    margin-top: 6px;
  }
  .contacts {
    position: absolute;
    top: 138px;
    left: 34px;
    list-style: none;
  }
  .contacts__item {
    display: flex;
    align-items: center;
    gap: 8px;
    color: var(--text-grey);
    font-size: 13px;
    line-height: 20px;
  }
  .contacts__icon { width: 12px; height: 12px; flex: none; }
  .brand {
    position: absolute;
    top: 150px;
    right: 40px;
    display: flex;
    flex-direction: column;
    align-items: center;
    gap: 6px;
  }
  .brand__square {
    width: 26px;
    height: 26px;
    background: var(--brand-blue);
    border-radius: 3px;
  }
  .brand__name {
    color: var(--brand-blue);
    font-weight: 600;
    font-size: 22px;
    letter-spacing: 1px;
    text-transform: uppercase;
  }
  .address {
    position: absolute;
    bottom: 28px;
    right: 70px;
    color: var(--text-grey);
    font-size: 13px;
    font-weight: 600;
    line-height: 17px;
    font-style: normal;
  }

  /* Back */
  .appointment {
    position: absolute;
    top: 40px;
    left: 40px;
    width: 230px;
  }
  .appointment__title {
    color: var(--brand-blue);
    font-size: 15px;
    font-weight: 700;
    margin-bottom: 10px;
  }
  .appointment__field {
    display: flex;
    align-items: flex-end;
    gap: 6px;
    color: var(--mid-blue);
    font-size: 12px;
    height: 24px;
  }
  .appointment__line {
    flex: 1;
    border-bottom: 1px solid var(--rule-grey);
    height: 1px;
    margin-bottom: 3px;
  }
  .back-square {
    position: absolute;
    right: 48px;
    bottom: 48px;
    width: 140px;
    height: 100px;
    background: var(--brand-blue);
    border-radius: 6px;
  }
</style>
</head>
<body>
<main class="canvas">
  <section class="card card--front" aria-label="Business card front">
    <header class="holder">
      <h1 class="holder__name">Liam Dorsett<span class="holder__post">BDT,</span></h1>
      <p class="holder__quals">PGDipCDentTech Calverin</p>
      <p class="holder__role">Dental Prosthetist</p>
    </header>

    <ul class="contacts">
      <li class="contacts__item">
        <svg class="contacts__icon" viewBox="0 0 12 12" aria-hidden="true">
          <rect width="12" height="12" rx="1.5" fill="#0255a3"/>
          <path d="M3.5 2.8l1.3 1.4-.7.9c.5 1 1.3 1.8 2.3 2.3l.9-.7 1.4 1.3-.9 1.2C5.8 9 3 6.2 2.8 3.7z" fill="#fbfbfb"/>
        </svg>
        0800 47 3125
      </li>
      <li class="contacts__item">
        <svg class="contacts__icon" viewBox="0 0 12 12" aria-hidden="true">
          <rect width="12" height="12" rx="1.5" fill="#0255a3"/>
          <path d="M3.5 2.8l1.3 1.4-.7.9c.5 1 1.3 1.8 2.3 2.3l.9-.7 1.4 1.3-.9 1.2C5.8 9 3 6.2 2.8 3.7z" fill="#fbfbfb"/>
        </svg>
        09 572 1394
      </li>
      <li class="contacts__item">
        <svg class="contacts__icon" viewBox="0 0 12 12" aria-hidden="true">
          <rect width="12" height="12" rx="1.5" fill="#0255a3"/>
          <rect x="2.5" y="3.5" width="7" height="5" fill="none" stroke="#fbfbfb" stroke-width="1"/>
          <path d="M2.5 3.5L6 6.4 9.5 3.5" fill="none" stroke="#fbfbfb" stroke-width="1"/>
        </svg>
        liam@veltrimora.co.nz
      </li>
      <li class="contacts__item">
        <svg class="contacts__icon" viewBox="0 0 12 12" aria-hidden="true">
          <rect width="12" height="12" rx="1.5" fill="#0255a3"/>
          <circle cx="6" cy="6" r="3.5" fill="none" stroke="#fbfbfb" stroke-width="0.9"/>
          <ellipse cx="6" cy="6" rx="1.5" ry="3.5" fill="none" stroke="#fbfbfb" stroke-width="0.8"/>
          <path d="M2.5 6h7" stroke="#fbfbfb" stroke-width="0.8"/>
        </svg>
        www.veltrimora.co.nz
      </li>
    </ul>

    <div class="brand">
      <span class="brand__square" aria-hidden="true"></span>
      <span class="brand__name">Veltrimora</span>
    </div>

    <address class="address">
      14 Marlow Crest Road<br>
      Halbrook West<br>
      Auckland 0793
    </address>
  </section>

  <section class="card card--back" aria-label="Business card back">
    <div class="appointment">
      <h2 class="appointment__title">Your next appointment</h2>
      <div class="appointment__field">Date <span class="appointment__line"></span></div>
      <div class="appointment__field">Time <span class="appointment__line"></span></div>
    </div>
    <span class="back-square" aria-hidden="true"></span>
  </section>
</main>
</body>
</html>
```